Exciting & Elegant Stationary Pack

Stationary consists of
1. Letter head / Envelope
2. Business Card
3. Invoice
4. 40x40mm sticker

Attached files;

1. Logo (Other formats available on request)
2. MS word Doc - For information and description of design
3. Website image (This will be our new website so use the colours so everything ties together)
4. Sample of stationary pack we like, but feel free to be creative

Target Market(s)

Home improvement

Industry/Entity Type

Construction

Font styles to use
Other font styles liked:
• Leave up to designer - We like font used on (website attached image)

Requirements
Must have
• Please look at uploaded file of sample website and use colours
Nice to have
• Any type of business card design - eg. metal, die cut, embossed, etc...

```html
<!DOCTYPE html>
<html lang="en">
<head>
<meta charset="utf-8">
<title>Grout &amp; Grain Stationery</title>
<link rel="stylesheet" href="https://fonts.googleapis.com/css2?family=Montserrat:wght@400;500;700;800&display=swap">
<style>
  :root {
    --red: #d0262f;
    --navy: #1a4672;
    --white: #ffffff;
    --ink: #1d2b3f;
    --page: #ececec;
  }
  * { margin: 0; padding: 0; box-sizing: border-box; }
  html, body { width: 1200px; height: 2640px; overflow: hidden; }
  body {
    position: relative;
    background: var(--page);
    font-family: "Montserrat", Arial, sans-serif;
    color: var(--ink);
  }
  .card {
    position: absolute;
    left: 100px;
    width: 1000px;
    height: 572px;
    border-radius: 28px;
    overflow: hidden;
  }
  .card-front { top: 100px; background: var(--red); }
  .card-back { top: 772px; background: var(--white); }
  .band { position: absolute; inset: 0; width: 100%; height: 100%; }
  .wordmark {
    position: absolute;
    color: var(--white);
    font-weight: 800;
    line-height: 1;
    letter-spacing: 2px;
    text-transform: uppercase;
  }
  .card-front .wordmark { left: 300px; top: 150px; font-size: 96px; }
  .card-back .wordmark { left: 600px; top: 250px; font-size: 58px; }
  .back-heading {
    position: absolute;
    right: 80px;
    top: 78px;
    color: var(--navy);
    font-weight: 800;
    font-size: 36px;
    text-transform: uppercase;
  }
  .accent-bar {
    position: absolute;
    left: 0;
    top: 118px;
    width: 18px;
    height: 82px;
    background: var(--red);
  }
  .person { position: absolute; left: 66px; top: 116px; }
  .person-name { color: var(--navy); font-weight: 700; font-size: 38px; }
  .person-role { color: var(--red); font-weight: 500; font-size: 24px; margin-top: 4px; }
  .contact-list {
    position: absolute;
    left: 66px;
    top: 300px;
    list-style: none;
    font-size: 25px;
    line-height: 42px;
    color: var(--navy);
  }
  .contact-list .label { color: var(--red); font-weight: 700; }
  .section-title {
    position: absolute;
    left: 0;
    width: 1200px;
    top: 1420px;
    text-align: center;
    font-size: 64px;
    font-weight: 500;
    color: var(--ink);
  }
  .sticker {
    position: absolute;
    width: 480px;
    height: 480px;
    background: var(--red);
    overflow: hidden;
  }
  .sticker-1 { left: 80px; top: 1560px; }
  .sticker-2 { left: 640px; top: 1560px; }
  .sticker-3 { left: 360px; top: 2100px; }
  .sticker-info {
    position: absolute;
    left: 0;
    width: 100%;
    top: 42px;
    text-align: center;
    color: var(--white);
    font-size: 19px;
    line-height: 27px;
    font-weight: 500;
  }
  .sticker-info .brand { color: var(--navy); font-weight: 800; text-transform: uppercase; }
  .sticker-info .label { color: var(--navy); font-weight: 700; }
  .sticker .wordmark { left: 70px; top: 190px; font-size: 66px; }
</style>
</head>
<body>

  <section class="card card-front" aria-label="Business card front">
    <svg class="band" viewBox="0 0 1000 572" preserveAspectRatio="none" aria-hidden="true">
      <polygon points="330,330 800,150 1000,330 1000,572 560,572" fill="var(--navy)"/>
    </svg>
    <div class="wordmark">Grout &amp;<br>Grain</div>
  </section>

  <section class="card card-back" aria-label="Business card back">
    <svg class="band" viewBox="0 0 1000 572" preserveAspectRatio="none" aria-hidden="true">
      <polygon points="570,230 1000,230 1000,572 780,572 570,380" fill="var(--navy)"/>
    </svg>
    <h2 class="back-heading">Grout &amp; Grain</h2>
    <span class="accent-bar"></span>
    <div class="person">
      <p class="person-name">Minh Tran</p>
      <p class="person-role">Project Manager</p>
    </div>
    <ul class="contact-list">
      <li><span class="label">M :</span> 0400 123 987</li>
      <li><span class="label">W :</span> www.groutandgrain.com.au</li>
      <li><span class="label">E :</span> hello@groutandgrain.com.au</li>
      <li><span class="label">L :</span> 204519c</li>
    </ul>
    <div class="wordmark">Grout &amp;<br>Grain</div>
  </section>

  <h2 class="section-title">Stickers</h2>

  <section class="sticker sticker-1" aria-label="Sticker">
    <svg class="band" viewBox="0 0 480 480" preserveAspectRatio="none" aria-hidden="true">
      <polygon points="80,340 380,190 480,260 480,480 300,480" fill="var(--navy)"/>
    </svg>
    <div class="sticker-info">
      <p class="brand">Grout &amp; Grain</p>
      <p>PO Box 48 Fairview Park NSW 2170</p>
      <p><span class="label">M</span> 0400 123 987</p>
    </div>
    <div class="wordmark">Grout &amp;<br>Grain</div>
  </section>

  <section class="sticker sticker-2" aria-label="Sticker">
    <svg class="band" viewBox="0 0 480 480" preserveAspectRatio="none" aria-hidden="true">
      <polygon points="80,340 380,190 480,260 480,480 300,480" fill="var(--navy)"/>
    </svg>
    <div class="sticker-info">
      <p class="brand">Grout &amp; Grain</p>
      <p>PO Box 48 Fairview Park NSW 2170</p>
      <p><span class="label">M</span> 0400 123 987</p>
    </div>
    <div class="wordmark">Grout &amp;<br>Grain</div>
  </section>

  <section class="sticker sticker-3" aria-label="Sticker">
    <svg class="band" viewBox="0 0 480 480" preserveAspectRatio="none" aria-hidden="true">
      <polygon points="80,340 380,190 480,260 480,480 300,480" fill="var(--navy)"/>
    </svg>
    <div class="sticker-info">
      <p class="brand">Grout &amp; Grain</p>
      <p>PO Box 48 Fairview Park NSW 2170</p>
      <p><span class="label">M</span> 0400 123 987</p>
    </div>
    <div class="wordmark">Grout &amp;<br>Grain</div>
  </section>

</body>
</html>
```